Media Services Start-up -- Corporate Website and Logo Design. Inspiration required!

We need a logo design and corporate website design, including coding, for our start-up business.
Vennatra’s value proposition is based on bringing together media content from a vast number of geographies globally, adding human and AI curation, translation and editing, and delivering the content using tailored customer interfaces. On the one hand, the business brings together media coverage from all over the world, and on the other it brings together content, human skills and technology to deliver a supreme customer experience.
Vennatra is a B2B media monitoring and analytics business with emphasis on global customers. Vennatra's service offering is centred around sourcing media content from different markets, processing, storing and delivering the content and insights derived from it using an online platform / mobile app.
The messaging we want to create through the logo is:
- Global scope
- Speed of delivery
- Cost-efficiency
- Multi-lingual
- Tailor-made
- Trustworthy
Target Market(s)
Business to business, PR / Communications, Media, Marketing
Logo Text
Vennatra
Coding
Coded - Design and coding required
Number of Pages Required
5+ page
Font styles to use
Other font styles liked:
- See Design Brief for details
Colors
Designer to choose colors to be used in the design.

```html
<!DOCTYPE html>
<html lang="en">
<head>
<meta charset="utf-8">
<title>Vennatra — Home and Solutions</title>
<link href="https://fonts.googleapis.com/css2?family=Montserrat:wght@600;700;800&family=Open+Sans:wght@400;600;700&display=swap" rel="stylesheet">
<style>
:root{
  --board:#bdbec0;
  --ink:#2b2b2b;
  --body:#3d3d3d;
  --muted:#6d6d6d;
  --orange:#f15a22;
  --white:#ffffff;
  --rule:#e8e8e8;
  --disc:#f1f0f0;
  --footer:#5a5a5a;
}
*{margin:0;padding:0;box-sizing:border-box}
html,body{width:1200px;height:3283px;overflow:hidden}
body{background:var(--board);font-family:"Open Sans",Arial,sans-serif;color:var(--body);position:relative}

.page{position:absolute;left:61px;width:1066px;overflow:hidden}
.home{top:50px;height:639px}
.solutions{top:736px;height:2462px;background:var(--white)}

.hero-photo{position:absolute;inset:0}
.home .hero-photo{background:
  radial-gradient(ellipse at 55% 35%,#5c6470 0%,transparent 40%),
  radial-gradient(ellipse at 85% 80%,#1f5a9c 0%,transparent 35%),
  linear-gradient(160deg,#3a3f47 0%,#1e2b3f 45%,#10233f 100%)}
.solutions .hero-photo{height:370px;background:
  radial-gradient(ellipse at 75% 50%,#9a9a98 0%,transparent 40%),
  radial-gradient(ellipse at 40% 75%,#6d5a48 0%,transparent 40%),
  linear-gradient(170deg,#3b3d40 0%,#585b5e 50%,#4a4036 100%)}
.solutions .hero-photo::after{content:"";position:absolute;inset:0;background:rgba(30,30,30,.35)}

.topbar{position:absolute;left:0;top:0;width:100%;height:80px}
.logo{position:absolute;left:41px;top:28px;font-family:"Montserrat",sans-serif;font-weight:700;font-size:30px;color:var(--white);letter-spacing:.2px}
.nav{position:absolute;top:22px;left:0;width:100%;list-style:none}
.nav li{position:absolute;font-family:"Montserrat",sans-serif;font-weight:700;font-size:12.5px;color:var(--white);letter-spacing:.3px;white-space:nowrap}
.nav li.current{text-decoration:underline;text-underline-offset:5px;text-decoration-thickness:2px}

.intro-band{position:absolute;left:0;top:215px;width:423px;height:235px;background:rgba(20,22,26,.55)}
.intro-title{position:absolute;left:55px;top:245px;font-family:"Montserrat",sans-serif;font-weight:800;font-size:22px;line-height:32px;color:var(--white)}
.intro-text{position:absolute;left:55px;top:322px;width:370px;font-size:15.5px;line-height:21.5px;color:var(--white)}

.enquiry{position:absolute;left:656px;top:169px;width:296px;height:316px;background:rgba(60,64,70,.55);border:5px solid rgba(110,112,116,.55)}
.enquiry h2{position:absolute;left:31px;top:28px;font-family:"Montserrat",sans-serif;font-weight:700;font-size:20.5px;line-height:27px;color:var(--white)}
.field{position:absolute;left:33px;width:225px;height:36px;background:var(--white);font-size:10.5px;font-weight:600;color:#555;padding:11px 13px;text-transform:uppercase}
.cta{position:absolute;left:33px;top:228px;width:225px;height:46px;background:var(--orange);color:var(--white);font-family:"Montserrat",sans-serif;font-weight:700;font-size:18px;text-align:center;line-height:46px}

.legal-tab{position:absolute;left:419px;top:600px;width:225px;height:39px;background:rgba(15,15,15,.8);color:var(--white);font-size:11.5px;text-align:center;line-height:39px}

.page-title{position:absolute;left:0;top:160px;width:100%;text-align:center;font-family:"Montserrat",sans-serif;font-weight:800;font-size:40px;color:var(--white);letter-spacing:.5px}

.spine{position:absolute;left:491px;top:422px;width:2px;height:1926px;background:var(--rule)}
.divider{position:absolute;height:3px;width:377px;background:var(--rule)}

.spot-art{position:absolute;width:248px;height:248px;border-radius:50%;background:radial-gradient(circle at 50% 50%,#e6e5e5 0%,var(--disc) 60%)}

.service{position:absolute;width:430px}
.service h3{font-family:"Montserrat",sans-serif;font-weight:700;font-size:22px;color:var(--ink);line-height:28px;padding-bottom:5px;position:relative}
.service h3::after{content:"";position:absolute;left:0;bottom:-2px;width:84px;height:3px;background:var(--orange)}
.service ul{list-style:none;margin-top:28px}
.service li{position:relative;padding-left:23px;font-size:13px;line-height:17.8px;color:var(--body);margin-bottom:20px}
.service li svg{position:absolute;left:1px;top:3px;width:12px;height:10px}

.footer{position:absolute;left:0;bottom:0;width:100%;height:55px;background:var(--footer);color:#ddd;font-size:11.5px;text-align:center;line-height:55px}
</style>
</head>
<body>
<svg width="0" height="0" style="position:absolute">
  <defs>
    <symbol id="tick" viewBox="0 0 12 10"><path d="M1 5.2l3.4 3.3L11 1.5" fill="none" stroke="#6d6d6d" stroke-width="2.2"/></symbol>
  </defs>
</svg>

<section class="page home">
  <div class="hero-photo" role="img" aria-label="Analyst standing in a dark control room facing walls of blue data monitors"></div>
  <header class="topbar">
    <div class="logo">Vennatra</div>
    <ul class="nav">
      <li class="current" style="left:501px">HOME</li>
      <li style="left:568px">SOLUTIONS</li>
      <li style="left:670px">HOW WE DO IT</li>
      <li style="left:794px">OUR PEOPLE</li>
      <li style="left:903px">OUR TECHNOLOGY</li>
    </ul>
  </header>
  <div class="intro-band"></div>
  <h1 class="intro-title">DELIVERING GLOBAL<br>MEDIA INTELLIGENCE</h1>
  <p class="intro-text">Vennatra is an international media intelligence service provider. We help communications teams build and operate truly global media monitoring and measurement programmes.</p>
  <form class="enquiry">
    <h2>Learn more<br>about Vennatra</h2>
    <div class="field" style="top:90px">Name</div>
    <div class="field" style="top:137px">E mail</div>
    <div class="field" style="top:184px">Phone</div>
    <div class="cta">Get Started</div>
  </form>
  <div class="legal-tab">Copyright 2019 All Rights Reserved.</div>
</section>

<section class="page solutions">
  <div class="hero-photo" role="img" aria-label="Business people reviewing charts on a desk beside a laptop and phone"></div>
  <header class="topbar">
    <div class="logo">Vennatra</div>
    <ul class="nav">
      <li style="left:501px">HOME</li>
      <li class="current" style="left:568px">SOLUTIONS</li>
      <li style="left:670px">HOW WE DO IT</li>
      <li style="left:794px">OUR PEOPLE</li>
      <li style="left:903px">OUR TECHNOLOGY</li>
    </ul>
  </header>
  <h1 class="page-title">SOLUTIONS</h1>

  <div class="spine"></div>
  <div class="divider" style="left:115px;top:829px"></div>
  <div class="divider" style="left:491px;top:1155px"></div>
  <div class="divider" style="left:115px;top:1603px"></div>
  <div class="divider" style="left:491px;top:1997px"></div>

  <div class="spot-art" style="left:165px;top:480px" role="img" aria-label="Spot illustration: document list with an arrow, for content sourcing"></div>
  <article class="service" style="left:521px;top:426px;width:420px">
    <h3>Content Sourcing</h3>
    <ul>
      <li><svg><use href="#tick"/></svg>We help you build a content strategy that meets your budget and coverage needs across earned media - Print, Online, TV and Radio.</li>
      <li><svg><use href="#tick"/></svg>Identify geographies and markets of interest</li>
      <li><svg><use href="#tick"/></svg>Build target media source lists to fulfil monitoring and measurement requirements</li>
      <li><svg><use href="#tick"/></svg>Using our transparent cost calculator, we help you with accurate budgeting and choices to ensure you meet your strategy and objectives</li>
      <li><svg><use href="#tick"/></svg>Translate and localise keyword searches and editorial instructions into effecient source-/ country-/ provider-specific needs to minimise wasted content.</li>
    </ul>
  </article>

  <article class="service" style="left:117px;top:897px;width:340px">
    <h3>Content Collection</h3>
    <ul>
      <li><svg><use href="#tick"/></svg>We consolidate and manage the delivery of your global media content into a Cloud-based scalable media platform, taking the headache of content management away from your teams.</li>
    </ul>
  </article>
  <div class="spot-art" style="left:587px;top:848px" role="img" aria-label="Spot illustration: monitor showing charts, for content collection"></div>

  <div class="spot-art" style="left:162px;top:1223px" role="img" aria-label="Spot illustration: paper tray with a document, for content augmentation"></div>
  <article class="service" style="left:521px;top:1197px;width:450px">
    <h3>Content Augmentation</h3>
    <ul>
      <li><svg><use href="#tick"/></svg>We manage and normalise all of the source-level reference data - country, language, reach etc.</li>
      <li><svg><use href="#tick"/></svg>We add editorial validation to ensure only the content required reaches your delivery, removing inevitable noise from source providers</li>
      <li><svg><use href="#tick"/></svg>Tagging - AI and human based tagging to detect locations, people, topics, products, brands, services, etc.</li>
      <li><svg><use href="#tick"/></svg>Human and automated grouping of stories across geographies - clustering, "also-in" groupings etc.</li>
      <li><svg><use href="#tick"/></svg>Translation summarisation - AI Translation or human-created depending on budget, speed of delivery and need.</li>
      <li><svg><use href="#tick"/></svg>Digest authoring - refining the essence of today's coverage into a concise board-ready output for your organisation.</li>
    </ul>
  </article>

  <article class="service" style="left:117px;top:1654px;width:370px">
    <h3>Content Delivery</h3>
    <ul>
      <li><svg><use href="#tick"/></svg>Early morning delivery of a consolidated, ready-to-consume media coverage</li>
      <li><svg><use href="#tick"/></svg>Customised email templates, delivering content in templates designed to meet your needs</li>
      <li><svg><use href="#tick"/></svg>Customised platform - modern portal tailored to meet your media management needs, removing the unwanted clutter and focusing on the job at hand .</li>
      <li><svg><use href="#tick"/></svg>Integration with Intranets, third-party communication tools e.g. TeamChat, RSS readers, customised APIs.</li>
    </ul>
  </article>
  <div class="spot-art" style="left:587px;top:1665px" role="img" aria-label="Spot illustration: browser window layout, for content delivery"></div>

  <div class="spot-art" style="left:144px;top:2071px" role="img" aria-label="Spot illustration: laptop with a profile dashboard, for media insights"></div>
  <article class="service" style="left:521px;top:2044px;width:430px">
    <h3>Media Insights &amp; Consultancy</h3>
    <ul>
      <li><svg><use href="#tick"/></svg>Levering the normalised content sets from your integrated monitoring service, we can analyse and tag your coverage based on complex qualitative measurement criteria, consistent across all languages and geographies, to combine with quantitative metrics.</li>
      <li><svg><use href="#tick"/></svg>Consultancy to HQ and local offices on how to utilise and align existing measurement and insight intiatives to provide continuity.</li>
      <li><svg><use href="#tick"/></svg>Customised online dashboards with near real time data insights, coupled with Board-ready offline reporting and export options.</li>
      <li><svg><use href="#tick"/></svg>Integration with social media content, third-party data, point-of-sale, web analytics, and delivering on your Integrated Communications Framework</li>
    </ul>
  </article>

  <footer class="footer">Copyright 2019 All Rights Reserved.</footer>
</section>
</body>
</html>
```